BrindleStaffing Business Card Design

We are a staffing company finding positions for dedicated nurses and physicians.

Target Market(s)

Business Professionals

Industry/Entity Type

Staffing

Contact Information for Business Card

Gordon Pratley
Chairman
417 39th Avenue South
SAINT PETERSBURG FL 33712
813-555-4172 Mobile
813-555-8036 Fax
gpratley@brindlestaffing.com
www.brindlestaffing.com

Font styles to use
Sans Serif

Colors
fbee3e
f04a50
f37122

Requirements
Must have
• Logo Attached, see colors below. We'd like to see Yellow, Orange and Red.

```html
<!DOCTYPE html>
<html lang="en">
<head>
<meta charset="utf-8">
<title>BrindleStaffing Business Card</title>
<link rel="stylesheet" href="https://fonts.googleapis.com/css2?family=Open+Sans:wght@400;600;700&display=swap">
<style>
  :root {
    --backdrop: #1c1c1e;
    --paper: #ffffff;
    --brand-red: #f04a50;
    --brand-orange: #f37122;
    --brand-yellow: #fbee3e;
    --ink: #2b2b2b;
    --on-band: #ffffff;
  }
  * { box-sizing: border-box; margin: 0; padding: 0; }
  html, body {
    width: 1200px; height: 960px; overflow: hidden;
    background: var(--backdrop);
    font-family: "Open Sans", Arial, sans-serif;
  }
  .canvas { position: relative; width: 1200px; height: 960px; }
  .card {
    position: absolute; width: 640px; height: 366px;
    background: var(--paper); overflow: hidden;
    box-shadow: 0 10px 30px rgba(0,0,0,.45);
  }
  .card-front { left: 470px; top: 70px; }
  .card-back { left: 90px; top: 520px; }

  .front-brand {
    position: absolute; left: 0; right: 0; top: 128px;
    display: flex; flex-direction: column; align-items: center; gap: 18px;
  }
  .wordmark {
    display: flex; align-items: center; gap: 12px;
    font-weight: 700; color: var(--brand-orange); letter-spacing: -0.5px;
    white-space: nowrap;
  }
  .wordmark-dot { border-radius: 50%; background: var(--brand-yellow); flex: none; }
  .front-brand .wordmark { font-size: 56px; }
  .front-brand .wordmark-dot { width: 20px; height: 20px; }
  .front-url { font-size: 19px; letter-spacing: 2px; color: var(--ink); }

  .back-shape { position: absolute; inset: 0; }
  .back-brand { position: absolute; left: 40px; top: 146px; }
  .back-brand .wordmark { font-size: 30px; gap: 10px; }
  .back-brand .wordmark-dot { width: 13px; height: 13px; }

  .contact {
    position: absolute; right: 30px; top: 118px; width: 300px;
    text-align: right; color: var(--on-band);
  }
  .contact-name { font-size: 21px; font-weight: 700; line-height: 1.2; }
  .contact-title { font-size: 17px; margin-bottom: 14px; }
  .contact-address { font-size: 15px; line-height: 1.3; margin-bottom: 14px; }
  .contact-list { list-style: none; font-size: 15px; line-height: 1.5; }
  .contact-list li { display: flex; justify-content: flex-end; align-items: center; gap: 8px; }
  .contact-icon { width: 13px; height: 13px; flex: none; }
</style>
</head>
<body>
<main class="canvas">
  <section class="card card-front" aria-label="Card front">
    <div class="front-brand">
      <div class="wordmark"><span class="wordmark-dot"></span>BrindleStaffing</div>
      <div class="front-url">www.brindlestaffing.com</div>
    </div>
  </section>

  <section class="card card-back" aria-label="Card back">
    <svg class="back-shape" viewBox="0 0 640 366" width="640" height="366" aria-hidden="true">
      <path d="M358 0 C 382 110, 360 260, 180 366 L 640 366 L 640 0 Z" fill="var(--brand-red)"/>
      <path d="M344 0 C 368 110, 346 240, 206 318" fill="none" stroke="var(--brand-yellow)" stroke-width="7" stroke-linecap="round"/>
    </svg>

    <div class="back-brand">
      <div class="wordmark"><span class="wordmark-dot"></span>BrindleStaffing</div>
    </div>

    <div class="contact">
      <p class="contact-name">Gordon Pratley</p>
      <p class="contact-title">Title</p>
      <p class="contact-address">417 39th Avenue South<br>Saint Petersburg FL 33712</p>
      <ul class="contact-list">
        <li>813-555-4172
          <svg class="contact-icon" viewBox="0 0 16 16"><circle cx="8" cy="8" r="7.5" fill="#fff"/><path d="M5 4.5 L6.8 4.5 L7.4 6.6 L6.4 7.4 C6.9 8.6 7.6 9.3 8.7 9.7 L9.5 8.7 L11.5 9.3 L11.5 11 C8 11.3 4.8 8.2 5 4.5Z" fill="var(--brand-red)"/></svg>
        </li>
        <li>gpratley@brindlestaffing.com
          <svg class="contact-icon" viewBox="0 0 16 16"><circle cx="8" cy="8" r="7.5" fill="#fff"/><rect x="4" y="5.2" width="8" height="5.6" fill="none" stroke="var(--brand-red)" stroke-width="1.2"/><path d="M4 5.4 L8 8.4 L12 5.4" fill="none" stroke="var(--brand-red)" stroke-width="1.2"/></svg>
        </li>
        <li>www.brindlestaffing.com
          <svg class="contact-icon" viewBox="0 0 16 16"><circle cx="8" cy="8" r="7.5" fill="#fff"/><circle cx="8" cy="8" r="4.5" fill="none" stroke="var(--brand-red)" stroke-width="1.1"/><ellipse cx="8" cy="8" rx="2" ry="4.5" fill="none" stroke="var(--brand-red)" stroke-width="1"/><path d="M3.5 8 H12.5" stroke="var(--brand-red)" stroke-width="1"/></svg>
        </li>
      </ul>
    </div>
  </section>
</main>
</body>
</html>
```